We are a recruitment company based in Norwich/Cambridge England.
I have included our company logo which we want to remain the same.

What we are looking for is a new creative Business card which will really stand out!!

Contact Information for Business Card

Harriet Dunmore
email: Harriet@plavex.co.uk
Address: Brackwell House
Fenmoor Enterprise Park
Partridge Way
Norwich
QB9 3KX
Tel:01632 960418

```html
<!DOCTYPE html>
<html lang="en">
<head>
<meta charset="utf-8">
<title>Plavex Business Card</title>
<link rel="stylesheet" href="https://fonts.googleapis.com/css2?family=Quicksand:wght@500;600;700&display=swap">
<style>
  :root {
    --backdrop: #e8e3de;
    --card: #ffffff;
    --green: #8dc21f;
    --grey: #958c8f;
    --text: #5f5a5c;
    --shadow: rgba(60, 45, 35, 0.22);
  }
  * { margin: 0; padding: 0; box-sizing: border-box; }
  html, body {
    width: 1200px;
    height: 799px;
    overflow: hidden;
    background: var(--backdrop);
    font-family: "Quicksand", sans-serif;
  }
  .stage { position: relative; width: 1200px; height: 799px; }
  .card {
    position: absolute;
    top: 283px;
    width: 444px;
    height: 248px;
    background: var(--card);
    box-shadow: 0 2px 6px var(--shadow);
    overflow: hidden;
  }
  .card-front { left: 139px; }
  .card-back { left: 624px; }

  .brand {
    position: absolute;
    left: 0; right: 0;
    top: 96px;
    display: flex;
    justify-content: center;
    align-items: center;
    gap: 12px;
  }
  .brand-dot {
    width: 40px; height: 40px;
    border-radius: 50%;
    background: var(--green);
  }
  .brand-text { display: flex; flex-direction: column; }
  .brand-name {
    font-size: 40px;
    font-weight: 700;
    line-height: 1;
    color: var(--grey);
    letter-spacing: -0.5px;
  }
  .brand-tagline {
    font-size: 7px;
    font-weight: 600;
    letter-spacing: 1.6px;
    color: var(--grey);
    margin-top: 2px;
  }

  .card-decor { position: absolute; inset: 0; width: 444px; height: 248px; }
  .holder-name {
    position: absolute;
    right: 33px;
    top: 38px;
    font-size: 17px;
    font-weight: 700;
    color: var(--green);
    letter-spacing: 0.3px;
  }
  .contact-row {
    position: absolute;
    left: 98px;
    display: flex;
    align-items: flex-start;
    gap: 26px;
    font-size: 12.5px;
    font-weight: 500;
    color: var(--text);
    line-height: 15.3px;
  }
  .contact-row svg { width: 14px; height: 14px; flex: none; margin-top: 1px; }
  .contact-phone { top: 89px; }
  .contact-email { top: 125px; }
  .contact-address { top: 156px; }
</style>
</head>
<body>
<main class="stage">
  <section class="card card-front">
    <div class="brand">
      <span class="brand-dot"></span>
      <div class="brand-text">
        <span class="brand-name">Plavex</span>
        <span class="brand-tagline">Technology Recruitment</span>
      </div>
    </div>
  </section>

  <section class="card card-back">
    <svg class="card-decor" viewBox="0 0 377 210" aria-hidden="true">
      <defs>
        <filter id="arc-shadow" x="-20%" y="-20%" width="140%" height="140%">
          <feDropShadow dx="-1" dy="-1" stdDeviation="2" flood-color="#000" flood-opacity="0.25"/>
        </filter>
      </defs>
      <circle cx="0" cy="-10" r="140" fill="var(--grey)"/>
      <circle cx="0" cy="-10" r="98" fill="var(--green)"/>
      <circle cx="402.5" cy="200" r="110" fill="var(--grey)" filter="url(#arc-shadow)"/>
      <circle cx="402.5" cy="200" r="76" fill="var(--green)"/>
    </svg>

    <h1 class="holder-name">HARRIET DUNMORE</h1>

    <div class="contact-row contact-phone">
      <svg viewBox="0 0 14 14" aria-hidden="true"><rect x="3" y="1" width="8" height="12" rx="1.5" fill="none" stroke="var(--grey)" stroke-width="1"/><line x1="6" y1="11" x2="8" y2="11" stroke="var(--grey)"/></svg>
      <span>01632 960418</span>
    </div>
    <div class="contact-row contact-email">
      <svg viewBox="0 0 14 14" aria-hidden="true"><rect x="1.5" y="3" width="11" height="8" fill="none" stroke="var(--green)" stroke-width="1"/><polyline points="1.5,3 7,8 12.5,3" fill="none" stroke="var(--green)" stroke-width="1"/></svg>
      <span>Harriet@plavex.co.uk</span>
    </div>
    <div class="contact-row contact-address">
      <svg viewBox="0 0 14 14" aria-hidden="true"><path d="M7 13 C4 9 3 7 3 5.5 A4 4 0 0 1 11 5.5 C11 7 10 9 7 13Z" fill="none" stroke="var(--green)" stroke-width="1"/><circle cx="7" cy="5.5" r="1.4" fill="none" stroke="var(--green)" stroke-width="1"/></svg>
      <address style="font-style:normal">Brackwell House<br>Fenmoor Enterprise Park<br>Partridge Way<br>Norwich<br>QB9 3KX</address>
    </div>
  </section>
</main>
</body>
</html>
```